High end Electrical/home automation Business Card

Need a card for a high end electrical and home automation company utilising the existing logo.
Phone
Email
Website

Like black look with raised detail. Don’t necessarily need to keep colour of logo it could be made grayscale or white etc

Target Market(s)

High end clients

Contact Information for Business Card

Brightmoor Electrical

Requirements
Must have
• Logo, phone, email, website, address

High end look
Nice to have
• Black background card
Raised font
Should not have
• Lots of colour

```html
<!DOCTYPE html>
<html lang="en">
<head>
<meta charset="utf-8">
<title>Brightmoor Electrical – Business Card</title>
<link href="https://fonts.googleapis.com/css2?family=Montserrat:wght@400;700;800&family=Oswald:wght@500&display=swap" rel="stylesheet">
<style>
  :root {
    --bg: #b0b0ac;
    --card-white: #ffffff;
    --card-black: #3a3a3c;
    --edge-blue: #1591dd;
    --brand-blue: #1591dd;
    --ink: #333335;
    --emboss: #505053;
    --emboss-light: #5c5c60;
  }
  * { margin: 0; padding: 0; box-sizing: border-box; }
  html, body {
    width: 1200px; height: 801px; overflow: hidden;
    background: var(--bg);
    font-family: "Montserrat", sans-serif;
  }
  .stage {
    position: relative; width: 1200px; height: 801px;
    display: flex; align-items: center; justify-content: center; gap: 40px;
  }
  .card {
    position: relative; width: 540px; height: 309px;
    border-bottom: 6px solid var(--edge-blue);
    box-shadow: 0 14px 24px rgba(0,0,0,0.22);
  }
  .card-front { background: var(--card-white); }
  .card-back { background: var(--card-black); display: flex; align-items: center; justify-content: center; }

  .front-brand {
    position: absolute; left: 40px; top: 58px;
    display: flex; align-items: center; gap: 12px;
  }
  .brand-dot { width: 22px; height: 22px; border-radius: 50%; background: var(--brand-blue); }
  .brand-name {
    font-weight: 800; font-size: 26px; color: var(--ink); letter-spacing: -0.3px;
  }

  .person { position: absolute; left: 40px; top: 182px; }
  .person-name {
    font-family: "Oswald", sans-serif; font-weight: 500;
    font-size: 36px; line-height: 1; color: var(--brand-blue); letter-spacing: 0.5px;
    white-space: nowrap;
  }
  .person-role { font-size: 14px; color: var(--ink); margin-top: 6px; text-align: right; }

  .divider {
    position: absolute; left: 322px; top: 150px; width: 1px; height: 100px;
    background: var(--brand-blue);
  }

  .contact {
    position: absolute; left: 340px; top: 150px;
    list-style: none; font-size: 12px; color: var(--ink); line-height: 1.65;
  }
  .contact li { display: flex; align-items: center; gap: 7px; white-space: nowrap; }
  .contact .icon { width: 10px; height: 10px; flex: none; }
  .contact .spacer { width: 10px; flex: none; }

  .back-brand {
    display: flex; align-items: center; gap: 14px;
    font-weight: 800; font-size: 34px; color: var(--emboss); letter-spacing: -0.4px;
  }
  .back-dot { width: 26px; height: 26px; border-radius: 50%; background: var(--emboss-light); }
</style>
</head>
<body>
<main class="stage">
  <section class="card card-front" aria-label="Business card front">
    <div class="front-brand">
      <span class="brand-dot"></span>
      <span class="brand-name">Brightmoor Electrical</span>
    </div>

    <div class="person">
      <p class="person-name">DANIEL HARTLEY</p>
      <p class="person-role">Founder</p>
    </div>

    <span class="divider"></span>

    <ul class="contact">
      <li><span class="spacer"></span>418 Alder Court</li>
      <li><span class="spacer"></span>Colville, WA 99114</li>
      <li>
        <svg class="icon" viewBox="0 0 10 10"><path d="M2 1l2 0 1 2.4-1.2 1a5 5 0 0 0 2 2l1-1.2 2.2 1V9.2C8.8 9.6 1 9.8 1 2z" fill="var(--brand-blue)"/></svg>
        555 014 2286
      </li>
      <li>
        <svg class="icon" viewBox="0 0 10 10"><rect x="0.7" y="2" width="8.6" height="6" fill="none" stroke="var(--brand-blue)" stroke-width="1.2"/><path d="M0.7 2L5 5.4 9.3 2" fill="none" stroke="var(--brand-blue)" stroke-width="1.2"/></svg>
        hello@brightmoor.com
      </li>
      <li>
        <svg class="icon" viewBox="0 0 10 10"><circle cx="5" cy="5" r="4.3" fill="none" stroke="var(--brand-blue)" stroke-width="1.1"/><ellipse cx="5" cy="5" rx="1.9" ry="4.3" fill="none" stroke="var(--brand-blue)" stroke-width="0.9"/><path d="M0.7 5h8.6" stroke="var(--brand-blue)" stroke-width="0.9"/></svg>
        brightmoorelectrical.com
      </li>
    </ul>
  </section>

  <section class="card card-back" aria-label="Business card back">
    <div class="back-brand">
      <span class="back-dot"></span>
      <span>Brightmoor Electrical</span>
    </div>
  </section>
</main>
</body>
</html>
```